Garlic Farm for Farm Sales/Restaurant sales

Need a professional, but appealing to agriculture world. We are selling 27 kinds of Organic Garlic from a farm in Simla,CO. I have uploaded logo and business information-we are going to need a template, because I will need to use it for four separate people.
-We are trying to appeal to Farm to table restaurants
-As well as growers/farmers

Target Market(s)

Agriculture Sales/Restaurants-Organic

Industry/Entity Type

Agriculture

Contact Information for Business Card

Want it to look more unique then your average kelto stock card- I want it to look amazing

Font styles to use
Sans Serif

Colors
0455a3
ec1f27
fbed22
ffffff

Requirements
Must have
• Just be creative
Nice to have
• Colorful
Should not have
• plain

```html
<!DOCTYPE html>
<html lang="en">
<head>
<meta charset="utf-8">
<title>Plains Crest Garlic – Business Card</title>
<link rel="stylesheet" href="https://fonts.googleapis.com/css2?family=Montserrat:wght@400;500;700&display=swap">
<style>
  :root {
    --blue: #0455a3;
    --red: #ec1f27;
    --yellow: #fbed22;
    --white: #ffffff;
    --black: #0b0b0b;
    --ink: #111111;
    --page: #e9e6e0;
  }
  * { margin: 0; padding: 0; box-sizing: border-box; }
  html, body { width: 1200px; height: 902px; overflow: hidden; }
  body {
    background: var(--page);
    font-family: "Montserrat", Arial, sans-serif;
    position: relative;
  }
  .card {
    position: absolute;
    top: 291px;
    width: 540px;
    height: 320px;
    border-radius: 4px;
    overflow: hidden;
    box-shadow: 0 8px 24px rgba(0,0,0,0.25);
  }
  .card-front { left: 40px; background: var(--black); }
  .card-back { left: 620px; background: var(--yellow); }

  .front-brand {
    position: absolute;
    inset: 0;
    display: flex;
    flex-direction: column;
    align-items: center;
    justify-content: center;
    gap: 16px;
  }
  .brand-dot {
    width: 84px; height: 84px;
    border-radius: 50%;
    background: var(--red);
  }
  .front-name {
    color: var(--blue);
    font-weight: 700;
    font-size: 40px;
    letter-spacing: 0.5px;
  }
  .front-tagline {
    color: var(--red);
    font-weight: 500;
    font-size: 18px;
    margin-top: -12px;
  }

  .back-band {
    position: absolute;
    left: 0; right: 0;
    top: 98px;
    height: 66px;
    background: var(--white);
    border-top: 4px solid var(--blue);
    border-bottom: 4px solid var(--blue);
  }
  .licences {
    position: absolute;
    left: 22px; top: 52px;
    font-size: 12px; font-weight: 500;
    line-height: 1.25;
    color: var(--ink);
  }
  .abn {
    position: absolute;
    right: 22px; top: 18px;
    font-size: 12px; font-weight: 500;
    color: var(--ink);
  }
  .back-brand {
    position: absolute;
    left: 0; right: 0; top: 180px;
    text-align: center;
  }
  .back-name {
    color: var(--blue);
    font-size: 26px;
    font-weight: 500;
    letter-spacing: 1px;
    text-transform: uppercase;
    line-height: 1;
  }
  .back-tagline {
    color: var(--red);
    font-size: 11px;
    font-weight: 500;
    letter-spacing: 1px;
    text-transform: uppercase;
    margin-top: 4px;
  }
  .contact {
    position: absolute;
    left: 0; right: 0; top: 232px;
    text-align: center;
    color: var(--ink);
    font-size: 12px;
    line-height: 1.35;
  }
  .contact .person { font-weight: 700; font-size: 16px; margin-bottom: 2px; }
</style>
</head>
<body>

  <section class="card card-front">
    <div class="front-brand">
      <span class="brand-dot"></span>
      <span class="front-name">Plains Crest Garlic</span>
      <span class="front-tagline">gourmet garlic</span>
    </div>
  </section>

  <section class="card card-back">
    <div class="back-band"></div>

    <p class="abn">ABN:48201937554</p>
    <p class="licences">elec lic:41276C<br>air con lic:L071842</p>

    <div class="back-brand">
      <div class="back-name">Plains Crest Garlic</div>
      <div class="back-tagline">Gourmet Garlic</div>
    </div>

    <div class="contact">
      <div class="person">Doran Fealy</div>
      <div>P: 0400 182 736</div>
      <div>E: admin@dfelec.com.au</div>
      <div>p.o box 4170 marlow nsw 2310</div>
    </div>
  </section>

</body>
</html>
```